Irrigation Business needs their business cards modernised and revamped

I would like to keep my current logo, colours and revamp the format of the card.

I would like the card to be clean yet important.

Im not sure if you include texture but i would like the named logo to be indented into the card etc.

show me something alive and free something thats clinical to the point yet has a feel of achievement. i would like people to go nice card.

Target Market(s)

high end clients, corporate, sports field manger, the guys that make the decisions

Industry/Entity Type

Business

Contact Information for Business Card

nformation to be included

Dean Harlow (Director)
0487305526
dean@kolvat.biz
www.kestonfieldworks.com

instagram logo
google logo
facebook logo

Colors

Designer to choose colors to be used in the design.

Requirements
Nice to have
• indentations a really nice feel to the card good texture

```html
<!DOCTYPE html>
<html lang="en">
<head>
<meta charset="utf-8">
<title>Keston Fieldworks — Business Card</title>
<link rel="stylesheet" href="https://fonts.googleapis.com/css2?family=Montserrat:wght@700&family=Oswald:wght@500&family=Mulish:wght@400&display=swap">
<style>
  :root {
    --backdrop: #161616;
    --card: #2f2f2f;
    --card-edge: #262626;
    --emboss-dark: #1f1f1f;
    --emboss-light: rgba(255,255,255,0.08);
    --foil: #b9b9b9;
    --foil-soft: #8d8d8d;
    --rule: #555555;
  }
  * { box-sizing: border-box; margin: 0; padding: 0; }
  html, body { width: 1200px; height: 900px; overflow: hidden; }
  body {
    background: var(--backdrop);
    display: flex;
    flex-direction: column;
    align-items: center;
    justify-content: center;
    gap: 44px;
  }
  .card {
    width: 620px;
    height: 354px;
    background: var(--card);
    border: 1px solid var(--card-edge);
    position: relative;
  }

  /* Front */
  .card--front {
    display: flex;
    flex-direction: column;
    align-items: center;
    justify-content: center;
    gap: 18px;
  }
  .brand-mark {
    width: 80px;
    height: 80px;
    border-radius: 50%;
    border: 3px solid var(--foil-soft);
  }
  .brand-name {
    font-family: "Montserrat", sans-serif;
    font-weight: 700;
    font-size: 27px;
    letter-spacing: 0.02em;
    color: var(--foil);
  }

  /* Back */
  .card--back {
    display: flex;
    flex-direction: column;
    align-items: center;
    justify-content: center;
  }
  .contact-block {
    display: flex;
    align-items: center;
    gap: 26px;
    margin-top: 30px;
  }
  .identity { text-align: right; }
  .identity__name {
    font-family: "Oswald", sans-serif;
    font-weight: 500;
    font-size: 30px;
    letter-spacing: 0.02em;
    text-transform: uppercase;
    color: var(--emboss-dark);
    text-shadow: 1px 1px 0 var(--emboss-light);
  }
  .identity__role {
    font-family: "Mulish", sans-serif;
    font-size: 15px;
    color: var(--emboss-dark);
    text-shadow: 1px 1px 0 var(--emboss-light);
  }
  .divider {
    width: 1px;
    height: 64px;
    background: var(--rule);
  }
  .details { list-style: none; display: flex; flex-direction: column; gap: 6px; }
  .details__item {
    display: flex;
    align-items: center;
    gap: 14px;
    font-family: "Mulish", sans-serif;
    font-size: 17px;
    letter-spacing: 0.03em;
    color: var(--foil);
  }
  .details__icon { width: 14px; height: 14px; flex: none; }
  .social {
    display: flex;
    gap: 10px;
    margin-top: 58px;
  }
  .social__dot {
    width: 20px;
    height: 20px;
    border-radius: 50%;
    background: var(--foil-soft);
  }
</style>
</head>
<body>
  <section class="card card--front" aria-label="Card front">
    <div class="brand-mark"></div>
    <div class="brand-name">KESTON FIELDWORKS</div>
  </section>

  <section class="card card--back" aria-label="Card back">
    <div class="contact-block">
      <div class="identity">
        <div class="identity__name">Dean Harlow</div>
        <div class="identity__role">Director</div>
      </div>
      <div class="divider"></div>
      <ul class="details">
        <li class="details__item">
          <svg class="details__icon" viewBox="0 0 24 24" fill="none" stroke="#b9b9b9" stroke-width="2"><path d="M5 3h4l2 5-3 2a12 12 0 0 0 6 6l2-3 5 2v4a2 2 0 0 1-2 2A17 17 0 0 1 3 5a2 2 0 0 1 2-2z"/></svg>
          <span>0487305526</span>
        </li>
        <li class="details__item">
          <svg class="details__icon" viewBox="0 0 24 24" fill="none" stroke="#b9b9b9" stroke-width="2"><rect x="2" y="5" width="20" height="14"/><path d="M2 5l10 8 10-8"/></svg>
          <span>dean@kolvat.biz</span>
        </li>
        <li class="details__item">
          <svg class="details__icon" viewBox="0 0 24 24" fill="none" stroke="#b9b9b9" stroke-width="2"><circle cx="12" cy="12" r="10"/><path d="M2 12h20M12 2c3 3 3 17 0 20M12 2c-3 3-3 17 0 20"/></svg>
          <span>www.kestonfieldworks.com</span>
        </li>
      </ul>
    </div>
    <div class="social" aria-label="Social profiles">
      <span class="social__dot"></span>
      <span class="social__dot"></span>
      <span class="social__dot"></span>
    </div>
  </section>
</body>
</html>
```